Bluecrest Learning Corps by graduating students from college in two years

Based on the logo design, create stationary and business cards for
Dr. Venrel T Oskamp, CEO, (703) 482-1736
and Marisa Deltoft, Respresentative, (301) 647-2208
Address: 4719 Pellham Court, Kestrel Station, VA 24517
Incorporate elelments of the logo

Target Market(s)

USA

Font styles to use
Other font styles liked:
• match with the logo type style

```html
<!DOCTYPE html>
<html lang="en">
<head>
<meta charset="utf-8">
<title>Bluecrest Learning Corps – Stationery</title>
<link rel="stylesheet" href="https://fonts.googleapis.com/css2?family=Arimo:wght@400;700&family=Libre+Baskerville:wght@400;700&family=Oswald:wght@300;700&family=Playfair+Display:ital,wght@1,700&display=swap">
<style>
  :root {
    --navy: #1c2261;
    --navy-card: #2b3270;
    --gold: #f9c22e;
    --ink: #1f255f;
    --paper: #ffffff;
    --bg-top: #d5dadd;
    --bg-bottom: #b9c0c5;
    --watermark: #eceaf5;
  }
  * { box-sizing: border-box; margin: 0; padding: 0; }
  html, body { width: 1200px; height: 916px; overflow: hidden; }
  body {
    position: relative;
    background: linear-gradient(180deg, var(--bg-top), var(--bg-bottom));
    font-family: "Libre Baskerville", Georgia, serif;
    color: var(--ink);
  }
  .sprites { position: absolute; width: 0; height: 0; }

  /* ---------- business cards ---------- */
  .card {
    position: absolute; left: 68px; width: 438px; height: 249px;
    background: var(--paper); overflow: hidden;
    box-shadow: 0 6px 14px rgba(0,0,0,.28);
  }
  .card--back { top: 66px; background: var(--navy-card); }
  .card--rep { top: 339px; }
  .card--ceo { top: 614px; }

  .card-back__seal {
    position: absolute; left: 169px; top: 45px; width: 100px; height: 100px;
    border-radius: 50%; background: var(--gold);
  }
  .card-back__name {
    position: absolute; left: 0; right: 0; top: 170px; text-align: center;
    font-size: 17px; font-weight: 700; color: var(--gold); letter-spacing: .5px;
  }

  .card__seal {
    position: absolute; left: 197px; top: 18px; width: 44px; height: 44px;
    border-radius: 50%; background: var(--navy);
  }
  .card__brand {
    position: absolute; left: 0; right: 0; top: 72px; text-align: center;
    font-size: 11px; font-weight: 700; color: var(--navy); letter-spacing: .3px;
  }
  .card__person { position: absolute; right: 244px; top: 136px; text-align: right; }
  .card__name { font-size: 17px; font-weight: 700; color: var(--gold); white-space: nowrap; line-height: 1.2; }
  .card__role { font-size: 10px; color: #222; margin-top: 1px; }
  .card__divider { position: absolute; left: 219px; top: 120px; width: 1.5px; height: 66px; background: var(--gold); }
  .card__contacts { position: absolute; left: 250px; top: 129px; list-style: none; }
  .card__contacts li { display: flex; align-items: center; gap: 8px; height: 15px; font-size: 10px; color: var(--ink); white-space: nowrap; }
  .icon { width: 10px; height: 10px; fill: var(--gold); flex: none; }
  .card__wave { position: absolute; left: 0; top: 0; width: 438px; height: 249px; }
  .card__address {
    position: absolute; left: 0; right: 0; top: 219px; text-align: center;
    font-size: 10px; color: #fff; letter-spacing: .3px;
  }

  /* ---------- letterhead ---------- */
  .letterhead {
    position: absolute; left: 563px; top: 66px; width: 558px; height: 787px;
    background: var(--paper); overflow: hidden;
    box-shadow: 0 6px 16px rgba(0,0,0,.28);
  }
  .letterhead__watermark {
    position: absolute; left: 107px; top: 225px; width: 340px; height: 340px;
    border-radius: 50%; border: 18px solid var(--watermark);
  }
  .letterhead__brand { position: absolute; left: 30px; top: 27px; display: flex; align-items: center; gap: 8px; }
  .letterhead__seal { width: 42px; height: 42px; border-radius: 50%; background: var(--navy); }
  .letterhead__brand-name { font-size: 12px; font-weight: 700; color: var(--navy); width: 110px; line-height: 1.35; }
  .letterhead__contacts { position: absolute; right: 30px; top: 27px; list-style: none; }
  .letterhead__contacts li { display: flex; justify-content: flex-end; align-items: center; gap: 10px; height: 15px; font-size: 10.5px; white-space: nowrap; }
  .letterhead__rule { position: absolute; left: 30px; top: 88px; width: 360px; height: 1px; background: var(--navy); }
  .letterhead__rule--gold { left: 390px; top: 87px; width: 138px; height: 3px; background: var(--gold); }

  .sender { position: absolute; left: 30px; top: 156px; }
  .person-name { font-family: "Oswald", "Arial Narrow", sans-serif; font-size: 26px; line-height: 1.1; color: var(--navy); white-space: nowrap; }
  .person-name b { font-weight: 700; }
  .person-name span { font-weight: 300; }
  .person-role { font-family: "Arimo", Arial, sans-serif; font-weight: 700; font-size: 11px; color: var(--navy); margin: 1px 0 0 2px; }
  .letter__date { position: absolute; right: 30px; top: 166px; font-family: "Arimo", Arial, sans-serif; font-weight: 700; font-size: 13.5px; color: var(--navy); }
  .sender__contacts { position: absolute; left: 30px; top: 214px; list-style: none; font-family: "Arimo", Arial, sans-serif; }
  .sender__contacts li { display: flex; align-items: center; gap: 6px; height: 13px; font-size: 10.5px; color: var(--navy); }
  .sender__contacts .icon { fill: var(--navy); width: 9px; height: 9px; }

  .letter__body { position: absolute; left: 30px; top: 277px; width: 498px; font-family: "Arimo", Arial, sans-serif; font-size: 12.2px; line-height: 16px; color: var(--navy); text-align: justify; }
  .letter__body p + p { margin-top: 16px; }

  .signature { position: absolute; left: 30px; top: 553px; width: 190px; height: 60px; background: linear-gradient(90deg, #eef0f7, #f7f8fc); }
  .signer { position: absolute; left: 30px; top: 616px; }

  .letterhead__wave { position: absolute; left: 0; top: 0; width: 558px; height: 787px; }
  .letterhead__address { position: absolute; left: 0; right: 0; top: 760px; display: flex; justify-content: center; align-items: center; gap: 8px; font-size: 11px; color: #fff; letter-spacing: .3px; }
  .letterhead__address .icon { fill: #fff; width: 11px; height: 12px; }

  /* ---------- labels ---------- */
  .label { position: absolute; top: 866px; font-family: "Playfair Display", Georgia, serif; font-style: italic; font-weight: 700; font-size: 30px; color: #fff; text-shadow: 0 1px 3px rgba(0,0,0,.25); letter-spacing: 1px; }
  .label--cards { left: 146px; }
  .label--letterhead { left: 727px; top: 856px; }
</style>
</head>
<body>

<svg class="sprites" aria-hidden="true">
  <symbol id="i-phone" viewBox="0 0 24 24"><path d="M6.6 10.8a15.1 15.1 0 0 0 6.6 6.6l2.2-2.2a1 1 0 0 1 1-.25 11.4 11.4 0 0 0 3.6.57 1 1 0 0 1 1 1V20a1 1 0 0 1-1 1A17 17 0 0 1 3 4a1 1 0 0 1 1-1h3.5a1 1 0 0 1 1 1c0 1.25.2 2.45.57 3.57a1 1 0 0 1-.25 1z"/></symbol>
  <symbol id="i-globe" viewBox="0 0 24 24"><path d="M12 2a10 10 0 1 0 0 20 10 10 0 0 0 0-20zm-1 17.9A8 8 0 0 1 4.1 10L9 15v1a2 2 0 0 0 2 2zm6.9-2.5A2 2 0 0 0 16 16h-1v-3a1 1 0 0 0-1-1H8v-2h2a1 1 0 0 0 1-1V7h2a2 2 0 0 0 2-2v-.4a8 8 0 0 1 2.9 12.8z"/></symbol>
  <symbol id="i-mail" viewBox="0 0 24 24"><path d="M3 9l9-6 9 6v11a1 1 0 0 1-1 1H4a1 1 0 0 1-1-1zm2 1.2V19h14v-8.8l-7 4.6z"/></symbol>
  <symbol id="i-pin" viewBox="0 0 24 24"><path d="M12 2a7 7 0 0 0-7 7c0 5.2 7 13 7 13s7-7.8 7-13a7 7 0 0 0-7-7zm0 9.5A2.5 2.5 0 1 1 12 6.5a2.5 2.5 0 0 1 0 5z"/></symbol>
</svg>

<!-- business card: back -->
<section class="card card--back">
  <div class="card-back__seal"></div>
  <div class="card-back__name">Bluecrest Learning Corps</div>
</section>

<!-- business card: representative -->
<section class="card card--rep">
  <div class="card__seal"></div>
  <div class="card__brand">Bluecrest Learning Corps</div>
  <div class="card__person">
    <div class="card__name">Marisa Deltoft</div>
    <div class="card__role">Respresentative</div>
  </div>
  <div class="card__divider"></div>
  <ul class="card__contacts">
    <li><svg class="icon"><use href="#i-phone"/></svg>(301) 647-2208</li>
    <li><svg class="icon"><use href="#i-globe"/></svg>www.bluecrestcorps.org</li>
    <li><svg class="icon"><use href="#i-mail"/></svg>info@bluecrestcorps.org</li>
  </ul>
  <svg class="card__wave" viewBox="0 0 438 249" aria-hidden="true">
    <path d="M0 178 Q219 248 438 178 L438 249 L0 249Z" fill="var(--navy)"/>
    <path d="M16 174 Q219 240 422 174" fill="none" stroke="var(--gold)" stroke-width="3"/>
  </svg>
  <div class="card__address">4719 Pellham Court, Kestrel Station, VA 24517</div>
</section>

<!-- business card: CEO -->
<section class="card card--ceo">
  <div class="card__seal"></div>
  <div class="card__brand">Bluecrest Learning Corps</div>
  <div class="card__person">
    <div class="card__name">Dr. Venrel T Oskamp</div>
    <div class="card__role">CEO</div>
  </div>
  <div class="card__divider"></div>
  <ul class="card__contacts">
    <li><svg class="icon"><use href="#i-phone"/></svg>(703) 482-1736</li>
    <li><svg class="icon"><use href="#i-globe"/></svg>www.bluecrestcorps.org</li>
    <li><svg class="icon"><use href="#i-mail"/></svg>info@bluecrestcorps.org</li>
  </ul>
  <svg class="card__wave" viewBox="0 0 438 249" aria-hidden="true">
    <path d="M0 178 Q219 248 438 178 L438 249 L0 249Z" fill="var(--navy)"/>
    <path d="M16 174 Q219 240 422 174" fill="none" stroke="var(--gold)" stroke-width="3"/>
  </svg>
  <div class="card__address">4719 Pellham Court, Kestrel Station, VA 24517</div>
</section>

<!-- A4 letterhead -->
<section class="letterhead">
  <div class="letterhead__watermark"></div>

  <div class="letterhead__brand">
    <div class="letterhead__seal"></div>
    <div class="letterhead__brand-name">Bluecrest Learning Corps</div>
  </div>
  <ul class="letterhead__contacts">
    <li>(301) 647-2208<svg class="icon"><use href="#i-phone"/></svg></li>
    <li>www.bluecrestcorps.org<svg class="icon"><use href="#i-globe"/></svg></li>
    <li>info@bluecrestcorps.org<svg class="icon"><use href="#i-mail"/></svg></li>
  </ul>
  <div class="letterhead__rule"></div>
  <div class="letterhead__rule letterhead__rule--gold"></div>

  <div class="sender">
    <div class="person-name"><b>Orlena</b> <span>Vasko</span></div>
    <div class="person-role">Founder &amp; CEO</div>
  </div>
  <div class="letter__date">August-05-2019</div>
  <ul class="sender__contacts">
    <li><svg class="icon"><use href="#i-phone"/></svg>(817) 530-4192</li>
    <li><svg class="icon"><use href="#i-globe"/></svg>www.bluecrestcorps.org</li>
    <li><svg class="icon"><use href="#i-mail"/></svg>info@bluecrestcorps.org</li>
  </ul>

  <div class="letter__body">
    <p>Lorem ipsum dolor sit amet, consectetuer adipiscing elit, sed diam nonummy nibh euismod tincidunt ut laoreet dolore magna aliquam erat volutpat. Ut wisi enim ad minim veniam, quis nostrud exerci tation ullamcorper suscipit lobortis</p>
    <p>Lorem ipsum dolor sit amet, cons ectetuer adipiscing elit, sed diam nonummy nibh euismod tincidunt ut laoreet dolore magna aliquam erat volutpat. Ut wisi enim ad minim veniam, quis nostrud exerci tation ullamcorper suscipit lobortis nisl ut aliquip ex ea commodo consequat. Lorem ipsum dolor sit amet, consectetuer olutpat. Ut wisi enim ad minim veniam, quis nostrud exerci tation ullamcorper suscipit lobortis nisl ut aliquip ex ea commodo consequat. Duis autem</p>
    <p>vel eum iriure dolor in hendrerit in vulputate velit esse molestie consequat, vel illum dolore eu feugiat nulla facilisis at vero eros et accumsan et iusto odio dignissim qui blandit praesent luptatum zzril delenit augue duis dolore te feugait nulla facilisi. Lorem ipsum dolor sit amet, cons ectetuer adipiscing elit, sed diam nonummy nibh euismod tincidunt ut laoreet dolore magna aliquam erat volutpat. Ut wisi enim .</p>
  </div>

  <div class="signature" role="img" aria-label="Handwritten signature of the director"></div>
  <div class="signer">
    <div class="person-name"><b>Tamsin</b> <span>Corvell</span></div>
    <div class="person-role">Director</div>
  </div>

  <svg class="letterhead__wave" viewBox="0 0 558 787" aria-hidden="true">
    <path d="M0 705 Q279 800 558 705 V787 H0Z" fill="var(--navy)"/>
    <path d="M22 703 Q279 790 536 703" fill="none" stroke="var(--gold)" stroke-width="4"/>
  </svg>
  <div class="letterhead__address"><svg class="icon"><use href="#i-pin"/></svg>4719 Pellham Court, Kestrel Station, VA 24517</div>
</section>

<div class="label label--cards">Business card</div>
<div class="label label--letterhead">A4 Letterhead</div>

</body>
</html>
```